Oil and Gas Exploration and Production company needs a business card design

We need a business card design using our logo and colors in the logo. We want a mainstream design.

```html
<!DOCTYPE html>
<html lang="en">
<head>
<meta charset="utf-8">
<title>Andora Oil &amp; Gas – Business Card</title>
<link rel="stylesheet" href="https://fonts.googleapis.com/css2?family=Work+Sans:wght@400;500;700&display=swap">
<style>
  :root {
    --stage: #262626;
    --card-black: #0d0d0e;
    --card-white: #ffffff;
    --gold: #c89b3c;
    --ink: #1a1a1a;
    --paper-text: #ffffff;
  }
  * { box-sizing: border-box; margin: 0; padding: 0; }
  html, body { width: 1200px; height: 930px; overflow: hidden; }
  body {
    background: var(--stage);
    font-family: "Work Sans", Arial, sans-serif;
    position: relative;
  }
  .card {
    position: absolute;
    width: 560px;
    height: 320px;
    border-radius: 18px;
    box-shadow: 0 18px 40px rgba(0,0,0,0.45);
    overflow: hidden;
  }
  .card--back {
    left: 90px; top: 110px;
    background: var(--card-black);
    display: flex; align-items: center; justify-content: center;
  }
  .card--front {
    left: 550px; top: 500px;
    background: var(--card-white);
  }
  .brand {
    display: flex; align-items: center; gap: 14px;
    font-weight: 700;
    font-size: 34px;
    letter-spacing: 0.5px;
    white-space: nowrap;
  }
  .brand__dot {
    width: 26px; height: 26px; border-radius: 50%;
    background: var(--gold);
    flex: none;
  }
  .card--back .brand { color: var(--paper-text); }
  .card--front .brand {
    position: absolute; left: 30px; top: 160px;
    width: 250px;
    gap: 10px;
    color: var(--ink);
    font-size: 22px;
    letter-spacing: 0.2px;
  }
  .card--front .brand__dot { width: 20px; height: 20px; }
  .divider {
    position: absolute; left: 300px; top: 70px;
    width: 2px; height: 180px;
    background: var(--gold);
  }
  .contact {
    position: absolute; left: 324px; top: 70px;
    width: 220px;
    color: var(--ink);
    font-size: 13px; line-height: 1.35;
  }
  .contact__name {
    color: var(--gold);
    font-size: 24px; font-weight: 500;
    line-height: 1.1;
    white-space: nowrap;
  }
  .contact__title { margin-bottom: 12px; }
  .contact__address { margin-bottom: 12px; }
  .contact__line { display: flex; align-items: center; gap: 8px; white-space: nowrap; }
  .contact__line svg { width: 11px; height: 11px; flex: none; }
  .contact__accent { color: var(--gold); }
</style>
</head>
<body>
  <section class="card card--back" aria-label="Business card back">
    <div class="brand"><span class="brand__dot"></span>Andora Oil &amp; Gas</div>
  </section>

  <section class="card card--front" aria-label="Business card front">
    <div class="brand"><span class="brand__dot"></span>Andora Oil &amp; Gas</div>
    <div class="divider"></div>
    <div class="contact">
      <p class="contact__name">Dale Whitmore</p>
      <p class="contact__title">CFO</p>
      <p class="contact__address">2450 Meridian Ave,<br>Tulsa, Oklahoma US</p>
      <p class="contact__line">
        <svg viewBox="0 0 12 12" aria-hidden="true"><path d="M2.5 1l2 2-1 1.5c.7 1.4 1.6 2.3 3 3L8 6.5l2 2-1.3 1.8C5 10 2 7 1.7 3.3z" fill="var(--gold)"/></svg>
        (555) 310-2487
      </p>
      <p class="contact__line">
        <svg viewBox="0 0 12 12" aria-hidden="true"><rect x="1" y="2.5" width="10" height="7" fill="none" stroke="var(--gold)" stroke-width="1.2"/><path d="M1 3l5 3.5L11 3" fill="none" stroke="var(--gold)" stroke-width="1.2"/></svg>
        info@andoraoilgas.com
      </p>
      <p class="contact__line">
        <svg viewBox="0 0 12 12" aria-hidden="true"><circle cx="6" cy="6" r="4.7" fill="none" stroke="var(--gold)" stroke-width="1.1"/><path d="M1.3 6h9.4M6 1.3c-2.4 2.6-2.4 6.8 0 9.4M6 1.3c2.4 2.6 2.4 6.8 0 9.4" fill="none" stroke="var(--gold)" stroke-width="0.9"/></svg>
        <span>www.<span class="contact__accent">andoraoilgas</span>.com</span>
      </p>
    </div>
  </section>
</body>
</html>
```